New Company Logo & Responsive Website Design for Codeworks Heron

Codeworks Heron provides a white labeled, digital lending platform technology solutions to the mortgage industry via a SaaS model. Our target market is Mortgage Companies and Banks who are looking for innovative technology to assist both borrowers and loan originators with the lending process, while automating as much of he process as possible.

Codeworks Heron is our company name, and our modular software offerings Include the following Products:

1) Applicant Heron: A customizable, web based, point-of-sale application for borrowers to complete a loan application, and guide them through the mortgage process.

POS Definition
"A point of sale (POS) is the client-facing software solution that allows borrowers to create a customer portal, apply for a loan online, and seamlessly submit needed documentation."

2) Ledger Heron: A Mortgage Loan Origination System

LOS Definition
"A Mortgage Loan Origination System (LOS) is a platform that takes a completed loan application and facilitates the mortgage transaction from origination to post closing. LOS systems may include document management, pricing and eligibility engines, and compliance tools to decrease risk and increase loan manufacturing quality.

3) Dwelling Heron: A brandable, home search website

The LOS and POS definitions provided above are just for your understanding of what these products are, not to be included word-for-word as website content.

We are looking for designs that are elegant, convey technical competency, simple to navigate, and set us apart from the competition.

We are not set on any particular colors at this point, so feel free to choose the best colors for your particular designs.

Please include company logo, both desktop and mobile designs with a template design for the website sub pages.

Some Examples of Mortgage Technology Websites offering similar products. These are to show the typical content, not designs that we particularly like or dislike.

https://brantiq.example/
https://www.clearvantro.example/
https://www.abodefundbuddy.example/
https://www.debtquokka.example/
https://www.ternixapps.example/products/trail

Please send comments with additional questions.

Thank You For your participation.

Mortgage Companies

```html
<!DOCTYPE html>
<html lang="en">
<head>
<meta charset="utf-8">
<title>Codeworks Heron</title>
<link rel="stylesheet" href="https://fonts.googleapis.com/css2?family=Ubuntu:wght@500;700&family=Montserrat:wght@400;700&family=Lato:wght@400;700&family=Lora:wght@400&family=Arimo:wght@400;700&display=swap">
<style>
:root{
  --blue:#034487;
  --blue-line:#5b86e5;
  --red:#f11823;
  --ink:#111;
  --grey:#555;
  --white:#fff;
  --black:#000;
}
*{margin:0;padding:0;box-sizing:border-box}
html,body{width:1200px;height:3919px;overflow:hidden;background:var(--white)}
body{position:relative;font-family:'Lato',sans-serif;color:var(--ink)}
.abs{position:absolute}
.hero-bg{left:0;top:0;width:1200px;height:800px}
.logo{font-family:'Ubuntu',sans-serif;font-weight:700;color:var(--white);white-space:nowrap}
.site-logo{left:99px;top:20px;font-size:29px}
.nav{left:0;top:30px;width:1200px;font-size:15px;color:var(--white)}
.nav a{color:var(--white);text-decoration:none;position:absolute;white-space:nowrap}
.btn{display:flex;align-items:center;justify-content:center;background:var(--red);color:var(--white);font-family:'Lato',sans-serif;font-weight:700;border-radius:6px;text-decoration:none}
.login{left:940px;top:15px;width:145px;height:49px;border-radius:25px;font-size:18px;font-weight:400;font-family:'Montserrat',sans-serif}
.hero-kicker{left:0;width:1200px;top:138px;text-align:center;font-family:'Montserrat',sans-serif;font-size:33px;color:var(--white)}
.hero-title{left:0;width:1200px;top:184px;text-align:center;font-family:'Montserrat',sans-serif;font-weight:700;font-size:68px;color:var(--white);letter-spacing:1px;white-space:nowrap}
.hero-text{left:180px;width:840px;top:280px;text-align:center;font-size:15.5px;line-height:26px;color:var(--white)}
.demo{left:502px;top:376px;width:196px;height:48px;border-radius:24px;font-size:18px;font-weight:400;font-family:'Montserrat',sans-serif}
.devices{left:228px;top:461px;width:685px;height:345px;border-radius:14px;background:linear-gradient(135deg,#0b1d3a,#1a3f82 55%,#6b7fa8)}
.section-title{left:0;width:1200px;top:874px;text-align:center;font-family:'Ubuntu',sans-serif;font-weight:500;font-size:42px}
.section-rule{left:577px;top:927px;width:46px;height:3px;background:var(--blue)}
.photo{border-radius:50%}
.ring{border:1.5px solid var(--blue-line);border-radius:50%}
.svc-title{font-family:'Ubuntu',sans-serif;font-weight:700;font-size:43px;color:var(--blue);white-space:nowrap}
.svc-sub{font-family:'Ubuntu',sans-serif;font-weight:500;font-size:27px;color:#333}
.svc-text{font-size:18.5px;line-height:25.7px;color:var(--grey);text-align:justify}
.more{height:45px;width:168px;font-size:18px}
.about-band{left:141px;top:2552px;width:1059px;height:501px;background:var(--blue)}
.about-photo{left:0;top:2510px;width:598px;height:496px;background:linear-gradient(120deg,#6d7f95,#c6d3e3 60%,#8fb0d8)}
.about-kicker{left:665px;top:2604px;font-family:'Ubuntu',sans-serif;font-weight:500;font-size:30px;color:var(--white)}
.about-kicker-rule{left:665px;top:2640px;width:42px;height:3px;background:var(--white)}
.about-title{left:663px;top:2656px;font-family:'Montserrat',sans-serif;font-weight:700;font-size:40px;color:var(--white);white-space:nowrap}
.about-body{left:665px;top:2728px;width:445px;font-family:'Arimo',sans-serif;color:var(--white)}
.about-strong{font-size:12.5px;line-height:21.5px;font-weight:700}
.about-text{margin-top:20px;font-size:12.5px;line-height:21.5px}
.about-more{margin-top:20px;width:168px;height:45px;font-size:18px}
.testi-title{left:506px;top:3115px;font-family:'Ubuntu',sans-serif;font-weight:500;font-size:31px}
.testi-text{left:510px;top:3177px;width:500px;font-size:15.5px;line-height:27.5px;color:#444;text-align:justify}
.testi-name{left:510px;top:3360px;font-family:'Lora',serif;font-size:22px}
.arrow{width:46px;height:46px;border-radius:50%;background:var(--white);box-shadow:0 2px 8px rgba(0,0,0,.18);display:flex;align-items:center;justify-content:center}
.footer-bg{left:0;top:3455px;width:1200px;height:464px}
.f-head{top:3583px;font-family:'Ubuntu',sans-serif;font-weight:500;font-size:27px;color:var(--white)}
.f-list{top:3642px;list-style:none;font-size:16.5px;line-height:30px;color:var(--white)}
.f-list li{position:relative;padding-left:20px}
.f-list li::before{content:"»";position:absolute;left:0;color:var(--red);font-weight:700}
.f-contact{color:var(--white);font-size:16.5px;line-height:26px;white-space:nowrap}
.f-icon{left:557px}
.footer-logo{left:847px;top:3638px;font-size:58px;line-height:62px}
.f-rule{left:100px;top:3843px;width:998px;height:1px;background:#666}
.copyright{left:0;width:1200px;top:3871px;text-align:center;font-size:15px;color:var(--white)}
</style>
</head>
<body>

<svg class="abs hero-bg" viewBox="0 0 1200 800" aria-hidden="true">
  <path d="M0,0 H1200 V548 Q600,1040 0,593 Z" fill="var(--blue)"/>
</svg>

<header>
  <div class="abs logo site-logo">Codeworks Heron</div>
  <nav class="abs nav">
    <a href="#" style="left:383px">Home</a>
    <a href="#" style="left:453px">Product ⌄</a>
    <a href="#" style="left:552px">Features ⌄</a>
    <a href="#" style="left:656px">Integrations</a>
    <a href="#" style="left:774px">Security</a>
    <a href="#" style="left:862px">News</a>
  </nav>
  <a class="abs btn login" href="#">LOGIN</a>
</header>

<section>
  <div class="abs hero-kicker">WELCOME TO</div>
  <h1 class="abs hero-title">CODEWORKS HERON</h1>
  <p class="abs hero-text">Lorem ipsum dolor sit amet, consectetur adipiscing elit, sed do eiusmod tempor incididunt ut labore et dolore magna aliqua. Ut enim ad minim veniam, quis nostrud exercitation ullamco laboris nisi ut aliquip ex ea commodo consequat. Duis aute irure dolor in reprehenderit in voluptate velit esse cillum dolore eu fugiat nulla pariatur.</p>
  <a class="abs btn demo" href="#">REQUEST DEMO</a>
  <div class="abs devices" role="img" aria-label="Tablet, laptop and phone showing the Codeworks Heron platform"></div>
</section>

<section>
  <h2 class="abs section-title">Our Services</h2>
  <div class="abs section-rule"></div>

  <div class="abs ring" style="left:20px;top:994px;width:416px;height:416px"></div>
  <div class="abs photo" role="img" aria-label="Couple receiving house keys from an advisor" style="left:71px;top:997px;width:396px;height:396px;background:linear-gradient(135deg,#b58b6a,#e9d7c4 55%,#7a6a5c)"></div>
  <h3 class="abs svc-title" style="left:545px;top:1022px">Applicant Heron</h3>
  <div class="abs svc-sub" style="left:546px;top:1086px">POS Definition</div>
  <p class="abs svc-text" style="left:545px;top:1141px;width:557px">Lorem ipsum dolor sit amet, consectetur adipiscing elit, sed do eiusmod tempor incididunt ut labore et dolore magna aliqua. Ut enim aA customizable, web based, point-of-sale application for borrowers to complete a loan application, and guide them through the mortgage process.d minim veniam, quis nostrud exercitation ullamco laboris nisi ut aliquip ex ea commodo consequat.</p>
  <a class="abs btn more" href="#" style="left:541px;top:1330px">Readr More</a>

  <div class="abs ring" style="left:783px;top:1518px;width:396px;height:396px"></div>
  <div class="abs photo" role="img" aria-label="Hand passing house keys to another hand" style="left:738px;top:1500px;width:398px;height:398px;background:linear-gradient(135deg,#2a2522,#8c7666 50%,#e4dcd2)"></div>
  <h3 class="abs svc-title" style="left:100px;top:1527px">Ledger Heron</h3>
  <div class="abs svc-sub" style="left:102px;top:1591px">LOS Definition</div>
  <p class="abs svc-text" style="left:100px;top:1646px;width:557px">A Mortgage Loan Origination System (LOS) is a platform that takes a completed loan application and facilitates the mortgage transaction from origination to post closing. LOS systems may include document management, pricing and eligibility engines, and compliance tools to decrease risk and increase loan manufacturing quality.</p>
  <a class="abs btn more" href="#" style="left:97px;top:1835px">Readr More</a>

  <div class="abs ring" style="left:20px;top:2013px;width:416px;height:416px"></div>
  <div class="abs photo" role="img" aria-label="Smiling couple looking at a phone beside a laptop" style="left:71px;top:2009px;width:396px;height:396px;background:linear-gradient(135deg,#c9b08a,#8b6a52 45%,#d8dde4)"></div>
  <h3 class="abs svc-title" style="left:545px;top:2034px">Dwelling Heron</h3>
  <div class="abs svc-sub" style="left:546px;top:2098px">POS Definition</div>
  <p class="abs svc-text" style="left:545px;top:2153px;width:557px">A customizable, web based, point-of-sale application for borrowers to complete a loan application, and guide them through the mortgage process. A customizable, web based, point-of-sale application for borrowers to complete a loan application, and guide them through the mortgage process. A customizable, web based, point-of-sale application .</p>
  <a class="abs btn more" href="#" style="left:541px;top:2342px">Readr More</a>
</section>

<section>
  <div class="abs about-band"></div>
  <div class="abs about-photo" role="img" aria-label="Two businessmen shaking hands"></div>
  <div class="abs about-kicker">About Us</div>
  <div class="abs about-kicker-rule"></div>
  <h2 class="abs about-title">CODEWORKS HERON</h2>
  <div class="abs about-body">
    <p class="about-strong">Lorem ipsum dolor sit amet, consectetur adipiscing elit, sed do eiusmod tempor incididunt ut labore et dolore magna aliqua. Ut enim ad minim veniam, quis nostrud exercitation ullamco laboris nisi ut aliquip ex ea commodo consequat. Duis aute irure dolor in reprehenderit in voluptate velit esse cillum dolore eu fugiat nulla pariatur.</p>
    <p class="about-text">Lorem ipsum dolor sit amet, consectetur adipiscing elit, sed do eiusmod tempor incididunt ut labore et dolore magna aliqua. Ut enim ad minim veniam.</p>
    <a class="btn about-more" href="#">Readr More</a>
  </div>
</section>

<section>
  <div class="abs" style="left:217px;top:3145px;width:98px;height:98px;border-radius:50%;background:var(--blue)"></div>
  <div class="abs" style="left:352px;top:3334px;width:92px;height:92px;border-radius:50%;background:var(--red)"></div>
  <div class="abs photo" role="img" aria-label="Portrait of a smiling man with glasses at a laptop" style="left:208px;top:3154px;width:260px;height:260px;border:4px solid #1a1a1a;background:linear-gradient(160deg,#bcd0e6,#4a6a93 60%,#2b3d58)"></div>
  <div class="abs arrow" style="left:99px;top:3267px">
    <svg width="12" height="14" viewBox="0 0 12 14"><path d="M9,1 L2,7 L9,13 Z" fill="#111"/></svg>
  </div>
  <div class="abs arrow" style="left:1049px;top:3267px">
    <svg width="12" height="14" viewBox="0 0 12 14"><path d="M3,1 L10,7 L3,13 Z" fill="#bbb"/></svg>
  </div>
  <h2 class="abs testi-title">Testimonial</h2>
  <p class="abs testi-text">Lorem ipsum dolor sit amet, consectetur adipiscing elit, sed do eiusmod tempor incididunt ut labore et dolore magna aliqua. Ut enim ad minim veniam, quis nostrud exercitation ullamco laboris nisi ut aliquip ex ea commodo consequat. Duis aute irure dolor in reprehenderit in voluptate velit esse cillum dolore eu fugiat nulla pariatur.</p>
  <div class="abs testi-name">Mara Quill</div>
  <div class="abs" style="left:622px;top:3357px;width:34px;height:34px;border-radius:50%;background:var(--white);box-shadow:0 2px 6px rgba(0,0,0,.2)"></div>
</section>

<footer>
  <svg class="abs footer-bg" viewBox="0 0 1200 464" aria-hidden="true">
    <path d="M0,112 Q600,-100 1200,112 V464 H0 Z" fill="var(--black)"/>
    <path d="M0,112 Q600,-100 1200,112" fill="none" stroke="var(--blue)" stroke-width="12"/>
  </svg>

  <div class="abs f-head" style="left:116px">Quick link</div>
  <ul class="abs f-list" style="left:106px">
    <li>Home</li><li>Product</li><li>Features</li><li>Integrations</li><li>Security</li><li>News</li>
  </ul>

  <div class="abs f-head" style="left:325px">Help Links</div>
  <ul class="abs f-list" style="left:318px">
    <li>Terms &amp; Conditions</li><li>Privacy Policy</li><li>About Us</li><li>Support</li>
  </ul>

  <div class="abs f-head" style="left:557px">Contact Us</div>
  <svg class="abs f-icon" style="top:3647px" width="14" height="18" viewBox="0 0 14 18"><path d="M7,1 C3.5,1 1,3.6 1,6.8 C1,11 7,17 7,17 C7,17 13,11 13,6.8 C13,3.6 10.5,1 7,1 Z" fill="var(--white)"/><circle cx="7" cy="6.8" r="2.2" fill="var(--black)"/></svg>
  <div class="abs f-contact" style="left:593px;top:3641px">253 Lorem ipsum dolor<br>eiusmod&nbsp; 1140</div>
  <svg class="abs f-icon" style="top:3722px" width="15" height="15" viewBox="0 0 15 15"><path d="M3,1 L5.5,1 L6.5,4.5 L5,6 C6,8 7,9 9,10 L10.5,8.5 L14,9.5 L14,12 C14,13 13,14 12,14 C6,14 1,9 1,3 C1,2 2,1 3,1 Z" fill="var(--white)"/></svg>
  <div class="abs f-contact" style="left:593px;top:3718px">+ 1 555-014-2290</div>
  <svg class="abs f-icon" style="top:3777px" width="17" height="13" viewBox="0 0 17 13"><rect x="1" y="1" width="15" height="11" rx="1.5" fill="none" stroke="var(--white)" stroke-width="1.5"/><path d="M1.5,2 L8.5,7.5 L15.5,2" fill="none" stroke="var(--white)" stroke-width="1.5"/></svg>
  <div class="abs f-contact" style="left:591px;top:3771px">info@codeworksheron.example</div>

  <div class="abs logo footer-logo">Codeworks<br>Heron</div>

  <div class="abs f-rule"></div>
  <div class="abs copyright">Copyright © 2022 Codeworks Heron - All Rights Reserved.</div>
</footer>

</body>
</html>
```